Heron Loan Partners Business Card

We need a business card design for our mortgage servicing company. In addition to servicing the loans of homeowners, we help homeowners with purchasing their homes and any mortgage refinancing. We would like to see designs that use the colors in the logo attached below (gold-ish yellow and navy blue), and any other design you deem fit! The design should communicate a simpler life with smart mortgages provided by Heron.

```html
<!DOCTYPE html>
<html lang="en">
<head>
<meta charset="utf-8">
<title>Heron Loan Partners Business Card</title>
<link href="https://fonts.googleapis.com/css2?family=Arimo:ital,wght@0,400;0,700;1,400&display=swap" rel="stylesheet">
<style>
  :root {
    --backdrop: #2b2b2e;
    --gold: #cba33a;
    --navy: #1e1c50;
    --paper: #f6f6f8;
    --white: #ffffff;
  }
  * { box-sizing: border-box; margin: 0; padding: 0; }
  html, body {
    width: 1200px; height: 960px; overflow: hidden;
    background: var(--backdrop);
    font-family: "Arimo", Arial, sans-serif;
  }
  .card {
    position: absolute; left: 250px;
    width: 700px; height: 400px;
    border-radius: 24px; overflow: hidden;
    background: var(--paper);
  }
  .card-back { top: 50px; }
  .card-front { top: 510px; background: var(--gold); }
  .brand {
    position: absolute; display: flex; align-items: center; gap: 14px;
    color: var(--navy); font-weight: 700; white-space: nowrap;
  }
  .brand-dot { width: 18px; height: 18px; border-radius: 50%; background: var(--gold); flex: none; }
  .card-back .brand { left: 0; right: 0; top: 176px; justify-content: center; font-size: 44px; }
  .front-panel { position: absolute; inset: 0; }
  .card-front .brand {
    left: 414px; right: 24px; top: 188px;
    justify-content: center; font-size: 21px; gap: 9px;
  }
  .card-front .brand-dot { width: 12px; height: 12px; }
  .contact { position: absolute; left: 44px; top: 40px; color: var(--white); }
  .person-name { font-size: 30px; font-weight: 700; color: var(--navy); }
  .person-role { font-size: 17px; font-style: italic; margin-top: 2px; }
  .address { font-size: 17px; line-height: 1.3; margin-top: 20px; }
  .contact-list { list-style: none; margin-top: 16px; font-size: 17px; line-height: 1.35; }
  .contact-list li { display: flex; align-items: center; gap: 8px; }
  .contact-list svg { width: 14px; height: 14px; fill: var(--navy); flex: none; }
  .tagline { position: absolute; left: 44px; bottom: 44px; font-size: 19px; color: var(--white); }
</style>
</head>
<body>
  <section class="card card-back">
    <div class="brand"><span class="brand-dot"></span>Heron Loan Partners</div>
  </section>

  <section class="card card-front">
    <svg class="front-panel" viewBox="0 0 700 400" width="700" height="400">
      <path d="M478 0 L398 58 Q380 72 380 96 L400 400 L700 400 L700 0 Z" fill="var(--white)"/>
      <path d="M488 0 L414 54 Q396 68 396 92 L414 400 L700 400 L700 0 Z" fill="var(--paper)"/>
      <path d="M485 0 L410 55 Q392 69 392 94 L410 400" fill="none" stroke="var(--navy)" stroke-width="7"/>
    </svg>
    <div class="brand"><span class="brand-dot"></span>Heron Loan Partners</div>

    <div class="contact">
      <h1 class="person-name">Daniel Carter</h1>
      <p class="person-role">President</p>
      <p class="address">4127 Lakeside Avenue<br>Brookfield, NY 12345</p>
      <ul class="contact-list">
        <li><svg viewBox="0 0 16 16"><path d="M3 1l3 0 1 4-2 1.5c1 2 2.5 3.5 4.5 4.5L11 9l4 1v3c0 1-1 2-2 2C7 15 1 9 1 3c0-1 1-2 2-2z"/></svg>(555) 0142-7788</li>
        <li><svg viewBox="0 0 16 16"><path d="M1 3h14v10H1z"/><path d="M2 4.5l6 4.5 6-4.5" fill="none" stroke="var(--gold)" stroke-width="1.2"/></svg>name@Heron.com</li>
        <li><svg viewBox="0 0 16 16"><circle cx="8" cy="8" r="7"/></svg>www.Heron.com</li>
      </ul>
    </div>
    <p class="tagline">Simpler life with smart mortgages</p>
  </section>
</body>
</html>
```